Blockchain Analytics Firm Needs Logo And Website Design

We need a logo and a very basic website for a company based in Linköping, Sweden called 'Vextor'. We build custom machine learning and AI solutions for companies based on blockchain. We are not picky about the colors, but the design should communicate modernity and stability.
We like the following websites:
https://www.pallidwren.co.uk/
https://www.tormacapitalhouse.com/
Target Market(s)
Our customers are startups that have their own product based on blockchain or other distributed ledger technology.
Industry/Entity Type
It Company
Contact Information for Business Card
Name, title and email address
Logo Text
Our company name and "Blockchain Analytics"
Font styles to use
Colors
Designer to choose colors to be used in the design.
Requirements
Must have
- The website and logo need to be modern and clean. In the beginning, we will not be filling out all sections of the website (team, clients, etc.) but we will need to have these set up so we can eventually use them.
Nice to have
- We like angular graphics and some animations on the webpage would be nice.

```html
<!DOCTYPE html>
<html lang="en">
<head>
<meta charset="utf-8">
<title>Vextor – Blockchain Analytics</title>
<link href="https://fonts.googleapis.com/css2?family=Montserrat:wght@400;500;600;700&family=Open+Sans:wght@400;600;700&display=swap" rel="stylesheet">
<style>
:root{
  --red:#e8413a;
  --navy:#0b1220;
  --navy-2:#1a2a3c;
  --ink:#222;
  --muted:#555;
  --grey-band:#f1f1f3;
  --grey-band-2:#e9e9ec;
  --maroon:#a44c5c;
  --purple:#5a3fd8;
  --footer:#121212;
  --white:#fff;
}
*{margin:0;padding:0;box-sizing:border-box}
html,body{width:1200px;height:4500px;overflow:hidden}
body{position:relative;background:var(--white);font-family:"Open Sans",sans-serif;color:var(--ink)}
.abs{position:absolute}
h1,h2,h3,h4{font-family:"Montserrat",sans-serif;font-weight:500}
.btn{position:absolute;display:flex;align-items:center;justify-content:center;background:var(--red);color:var(--white);font-family:"Montserrat",sans-serif;font-weight:600;border-radius:4px}
.btn-sm{width:96px;height:30px;font-size:13px}
.brand{display:flex;align-items:center;gap:12px;font-family:"Montserrat",sans-serif;font-weight:700;color:var(--red)}
.brand-mark{width:34px;height:34px;background:var(--red)}

/* hero */
.hero{left:0;top:0;width:1200px;height:650px;background:radial-gradient(ellipse at 55% 40%,var(--navy-2),var(--navy) 70%)}
.hero .brand{left:140px;top:38px;font-size:40px}
.nav{right:130px;top:40px;display:flex;gap:28px;font-family:"Montserrat",sans-serif;font-size:15px;color:var(--white)}
.nav .active{color:var(--red)}
.hero-title{left:0;width:1200px;top:272px;text-align:center;color:var(--white);font-size:38px;font-weight:700}
.hero-sub{left:0;width:1200px;top:326px;text-align:center;color:#dfe4ec;font-size:15px}
.hero .btn{left:532px;top:378px;width:132px;height:42px;font-size:16px}

/* services */
.section-title{left:0;width:1200px;text-align:center;font-size:31px;color:var(--ink)}
.section-sub{left:0;width:1200px;text-align:center;font-size:14px;color:var(--muted)}
.service h3{font-size:22px;color:var(--ink);margin-bottom:18px}
.service p{font-size:13.5px;line-height:21px;color:var(--muted);width:345px}
.art{border-radius:6px}

/* about */
.about-video{left:470px;top:2300px;width:685px;height:385px;background:linear-gradient(135deg,#2a1c22,#0e0a10 55%,#3a2a2e);box-shadow:0 12px 30px rgba(0,0,0,.35)}
.about-box{left:130px;top:2440px;width:410px;height:330px;background:var(--maroon);color:var(--white);padding:48px 88px}
.about-box h2{font-size:31px;font-weight:400;margin-bottom:20px}
.about-box p{font-size:13.5px;line-height:20px;width:240px}
.about-box .btn{left:88px;top:248px;width:96px;height:30px;background:var(--white);color:var(--maroon);font-size:13px}

/* how it works */
.feature{width:220px;text-align:center}
.feature svg{display:block;margin:0 auto 40px}
.feature h4{font-size:14px;font-weight:700;letter-spacing:.5px;margin-bottom:12px}
.feature p{font-size:13px;line-height:19px;color:var(--muted)}

/* testimonials */
.quote-mark{left:362px;top:3540px;font-family:"Montserrat",sans-serif;font-size:110px;color:#bbb;line-height:1;height:70px;overflow:hidden}
.quote{left:420px;top:3570px;width:480px;font-size:17.5px;line-height:29px;color:#555}
.quote-name{left:420px;top:3750px;font-size:14px;font-weight:700;letter-spacing:.5px}
.dots{left:0;width:1200px;top:3796px;display:flex;justify-content:center;gap:8px}
.dots span{width:11px;height:11px;border:1px solid #bbb;border-radius:50%}
.dots .on{background:var(--red);border-color:var(--red)}

/* partners */
.partners{left:130px;top:3985px;width:940px;display:flex;justify-content:space-between;align-items:center}
.partner{width:118px;height:36px;background:#d8d8dc;border-radius:4px}

/* footer */
.footer{left:0;top:4110px;width:1200px;height:390px;background:var(--footer);color:#ddd}
.footer .brand{position:absolute;left:150px;top:118px;font-size:40px}
.footer h5{font-family:"Montserrat",sans-serif;font-size:13px;font-weight:700;color:var(--white);letter-spacing:.5px;margin-bottom:20px}
.footer ul{list-style:none;font-size:12.5px;line-height:17px}
.contact li{display:flex;gap:12px;margin-bottom:14px;width:210px}
.contact svg{flex:none;margin-top:2px}
.social li{display:flex;align-items:center;gap:10px;margin-bottom:14px}
.social .dot{width:22px;height:22px;border-radius:50%;background:#2d6fd1}
.copyright{left:0;width:1200px;top:4428px;text-align:center;font-size:12px;color:#ccc}
</style>
</head>
<body>

<!-- Hero -->
<header class="abs hero" role="img" aria-label="Dark blue network of connected glowing nodes">
  <div class="abs brand"><span class="brand-mark"></span>Vextor</div>
  <nav class="abs nav"><span class="active">Home</span><span>About Us</span><span>Services</span><span>Features</span><span>Blog</span><span>Contact Us</span></nav>
  <h1 class="abs hero-title">Blockchain Analytics</h1>
  <p class="abs hero-sub">Vextor is a data analytics startup that can quickly deploy custom machine learning</p>
  <a class="btn">Read more</a>
</header>

<!-- Background bands -->
<svg class="abs" style="left:0;top:880px" width="1200" height="1400" aria-hidden="true">
  <polygon points="0,260 360,140 1200,360 1200,560 620,620 0,470" fill="var(--grey-band)"/>
  <polygon points="0,1050 700,920 1200,1000 1200,1300 0,1300" fill="var(--grey-band)"/>
</svg>

<!-- Services -->
<h2 class="abs section-title" style="top:722px">Our Services</h2>
<p class="abs section-sub" style="top:768px">Lorem Ipsum is simply dummy text of the printing</p>

<div class="abs art" style="left:210px;top:890px;width:340px;height:330px;background:radial-gradient(circle,#cdeee0,#e8f6f1 70%)" role="img" aria-label="Illustration of a profile document with a target and charts"></div>
<div class="abs service" style="left:658px;top:955px">
  <h3>Detailed Risk Scoring</h3>
  <p>But I must explain to you how all this mistaken idea of denouncing pleasure and praising pain was born and I will give you a complete account of the system, and expound the actual teachings.</p>
</div>
<a class="btn btn-sm" style="left:658px;top:1120px">Read more</a>

<div class="abs art" style="left:640px;top:1320px;width:340px;height:340px;background:linear-gradient(160deg,#3a4d6e,#1c2740)" role="img" aria-label="Illustration of server racks connected by cables"></div>
<div class="abs service" style="left:220px;top:1375px">
  <h3>Secure Infrastructure</h3>
  <p>But I must explain to you how all this mistaken idea of denouncing pleasure and praising pain was born and I will give you a complete account of the system, and expound the actual teachings.</p>
</div>
<a class="btn btn-sm" style="left:220px;top:1543px">Read more</a>

<div class="abs art" style="left:70px;top:1820px;width:500px;height:300px;background:linear-gradient(135deg,#e8eef6,#f6e6c9)" role="img" aria-label="Illustration of a laptop with design tools and a small city model"></div>
<div class="abs service" style="left:658px;top:1872px">
  <h3>Interoperability</h3>
  <p>But I must explain to you how all this mistaken idea of denouncing pleasure and praising pain was born and I will give you a complete account of the system, and expound the actual teachings.</p>
</div>
<a class="btn btn-sm" style="left:658px;top:2040px">Read more</a>

<!-- About -->
<svg class="abs" style="left:0;top:2230px" width="1200" height="630" aria-hidden="true">
  <polygon points="0,180 1200,0 1200,470 0,630" fill="var(--grey-band-2)"/>
</svg>
<div class="abs about-video" role="img" aria-label="Video still of a speaker presenting on stage, with a play button"></div>
<svg class="abs" style="left:788px;top:2468px" width="48" height="48" aria-hidden="true">
  <circle cx="24" cy="24" r="22" fill="none" stroke="#fff" stroke-width="2" opacity=".8"/>
  <polygon points="19,14 34,24 19,34" fill="#fff" opacity=".8"/>
</svg>
<div class="abs about-box">
  <h2>About Us</h2>
  <p>But I must explain to you how all this mistaken idea of denouncing pleasure and praising pain was born and I will give you a complete account of the system, and expound the actual teachings.</p>
  <a class="btn">Read more</a>
</div>

<!-- How it works -->
<h2 class="abs section-title" style="top:2908px;font-size:27px">How Vextor Works</h2>

<div class="abs feature" style="left:110px;top:3040px">
  <svg width="70" height="76" viewBox="0 0 70 76"><path d="M35 4 L64 14 V38 C64 56 50 68 35 73 C20 68 6 56 6 38 V14 Z" fill="none" stroke="var(--purple)" stroke-width="6"/><path d="M22 38 L32 48 L50 28" fill="none" stroke="var(--purple)" stroke-width="6"/></svg>
  <h4>SECURITY</h4>
  <p>But I must explain to you how all this mistaken idea of denouncing pleasure and praising pain was born.</p>
</div>
<div class="abs feature" style="left:355px;top:3040px">
  <svg width="70" height="76" viewBox="0 0 70 76"><rect x="28" y="2" width="14" height="8" fill="var(--purple)"/><circle cx="35" cy="44" r="28" fill="none" stroke="var(--purple)" stroke-width="6"/><path d="M35 44 V28 M35 44 L46 50" stroke="var(--purple)" stroke-width="5"/></svg>
  <h4>STABILITY</h4>
  <p>But I must explain to you how all this mistaken idea of denouncing pleasure and praising pain was born.</p>
</div>
<div class="abs feature" style="left:600px;top:3040px">
  <svg width="76" height="76" viewBox="0 0 76 76" fill="var(--purple)"><rect x="4" y="4" width="26" height="20" rx="3"/><rect x="46" y="4" width="26" height="20" rx="3"/><rect x="25" y="28" width="26" height="20" rx="3"/><rect x="4" y="52" width="26" height="20" rx="3"/><rect x="46" y="52" width="26" height="20" rx="3"/></svg>
  <h4>SCALABILITY</h4>
  <p>But I must explain to you how all this mistaken idea of denouncing pleasure and praising pain was born.</p>
</div>
<div class="abs feature" style="left:840px;top:3040px">
  <svg width="76" height="76" viewBox="0 0 76 76"><circle cx="38" cy="38" r="34" fill="var(--purple)"/><path d="M38 10 V66 M20 26 H32 M20 48 H32 M44 30 H56 M44 50 H56" stroke="#fff" stroke-width="4"/></svg>
  <h4>INTELLIGENT</h4>
  <p>But I must explain to you how all this mistaken idea of denouncing pleasure and praising pain was born.</p>
</div>

<!-- Testimonials -->
<svg class="abs" style="left:0;top:3330px" width="1200" height="600" aria-hidden="true">
  <polygon points="0,0 1200,110 1200,600 0,500" fill="var(--grey-band)"/>
</svg>
<h2 class="abs section-title" style="top:3470px;font-size:27px">Testimonials</h2>
<div class="abs quote-mark">&ldquo;</div>
<p class="abs quote">At vero eos et accusamus et iusto odio digni ssimos ducimus qui blanditiis prae sentium voluptatum deleniti atque corrupti quos dolor es et quas molestias excepturi sint occaecati cupiditate non provident, similique sunt in culpa qui officia deserunt mollitia animi, id est laborum et dolorum fuga.</p>
<p class="abs quote-name">MARTIN</p>
<div class="abs dots"><span></span><span></span><span class="on"></span><span></span><span></span></div>

<!-- Partners -->
<div class="abs partners">
  <span class="partner"></span><span class="partner"></span><span class="partner"></span><span class="partner"></span><span class="partner"></span><span class="partner"></span>
</div>

<!-- Footer -->
<footer class="abs footer">
  <div class="brand"><span class="brand-mark"></span>Vextor</div>
  <div class="abs" style="left:480px;top:70px">
    <h5>CONTACT US</h5>
    <ul class="contact">
      <li><svg width="10" height="13" viewBox="0 0 10 13"><path d="M5 0 C2 0 0 2 0 5 C0 8 5 13 5 13 C5 13 10 8 10 5 C10 2 8 0 5 0Z" fill="#ddd"/><circle cx="5" cy="5" r="2" fill="var(--footer)"/></svg>Norrvik Research Park, Tallgatan 12, 452 90 Ekvalla, SWEDEN</li>
      <li><svg width="11" height="11" viewBox="0 0 11 11"><path d="M2 0 L4 3 L3 4.5 C4 6.5 5 7.5 6.5 8 L8 7 L11 9 L9.5 11 C4 10 1 7 0 1.5Z" fill="#ddd"/></svg>013-555-0142</li>
      <li><svg width="12" height="9" viewBox="0 0 12 9"><rect width="12" height="9" fill="#ddd"/><path d="M0 0 L6 5 L12 0" fill="none" stroke="var(--footer)"/></svg>info@vextor.com</li>
    </ul>
  </div>
  <div class="abs" style="left:776px;top:70px">
    <h5>MENU</h5>
    <ul><li>Home</li><li>About Us</li><li>Services</li><li>Features</li><li>Blog</li><li>Contact Us</li></ul>
  </div>
  <div class="abs" style="left:940px;top:70px">
    <h5>CONNECT WITH US</h5>
    <ul class="social"><li><span class="dot"></span>Newsfeed</li><li><span class="dot"></span>Microblog</li><li><span class="dot"></span>Worknet</li></ul>
  </div>
</footer>
<p class="abs copyright">Copyrights @ 2018 All Rights Reserved</p>

</body>
</html>
```